Website front end design for an education nonprofit

This project involves design and development of the website front end (i.e., Web user interface and user experience design) for TAVO Sphere, a nonprofit initiative for developing an online platform for basic English language instruction, especially targeted toward underprivileged, non-native English speaking populations.

More about us: We are a team of educators, researchers and engineers passionate about this cause and would like to invite talented, creative web developers to join us in this effort to create positive social impact! Please send a personal message to the project owner for the executive summary to get more information about our initiative, big picture vision and the team.

TAVO Sphere website front end (UI/UX) design
Our key goals for this project are to develop an impressive Drupal-based front end for our website as well as to find really talented and creative web/UI/UX designers-cum-developers who are experts in the state-of-the-art web technologies, and are passionate about the cause of global online basic education. At the end of this project, we hope to have long term engagement with the selected developer(s) for our future website design and development needs.

Here are some preliminary guidelines on the TAVO Sphere website front end framework as envisioned by us so far. Please note that we would very much encourage creative ideas and mock-ups from the developers.

1. Current platform: Our website prototype back-end uses Drupal CMS (we plan to continue using Drupal CMS) and at the moment, a toy front-end is based on the Drupal Skeleton platform for its simplicity, clean UI and mobile device friendliness. The web developer / designer can choose any Drupal front end as a starting point or come up with a new Drupal template that meets our requirements below. Prior experience and expertise on Drupal would be great.

2. Audience profile: While the primary audience for the website is expected to be young kids (6-10 years) not very familiar with English, the secondary audience also includes adults interested in basic English language skills. So the overall goal is to have simple, uncluttered / clean, elegant and lightweight (think loading time as well as mobile device friendliness) interface that is extremely intuitive and easy to navigate, is artistic and aesthetically appealing to a wide audience (especially the non-native English speaking populations). The most important point is that our target audience should feel welcome with the clean, crisp look and easy, user-centric navigation, and should in no case feel overwhelmed (say with too much text or clutter on the front page).

3. Front page: Here is a currently envisioned preliminary sketch of the website front page (very much open for refinement and improvements)
a. The top “menu bar” part of the landing page will have our organization name and logo along with (or above) the top menu bar with the following links and sub-links
i. “Learn” link with sub-menu of all our content sections (World learning, Basic sentence learning, Classic short stories, Picture Dictionary)
ii. “About” links with information about us (sub-menu entries: About TAVO Sphere, Team, Supporters, Contributors)
iii. “Contribute” link with sub-menu entries Donate, Volunteer
iv. Menu entries towards the right side: “Login / sign up” followed by
v. “Search” with space to enter the search phrase
b. The middle “main page content” part of the page is where we would have entry points to our main content categories. The portion is envisioned to be graphical, with big blocks (images) as links to our content categories. The current categories (to start with) include 1. Word learning, 2. Basic sentence learning, and 3. Classic stories. We welcome creative ideas to represent these content categories in an appealing and elegant way (for example, these content categories could be portrayed as closed double doors that lead to the pages with the content. We would like to have placeholders for appropriate image links to different content categories – we should be able to put appropriate images or change them as we come up with new ideas that would work best with our target audience). The categories would change and grow as our content evolves, hence the core idea is to build a flexible framework that readily allows for expansion as well as customization.
c. The bottom menu / links bar portion of the landing page will have a list of links that are not included at the top. Examples include (with flexibility needed to add more when needed)
i. “Help”: this leads to a new page with FAQ, How to use
ii. “Contact us” link to a web contact form page
iii. “For Teachers” link to a page with information such as how to use, tips, pilot programs,
iv. “Volunteer” link to page with links such as Donate, Volunteer
v. “Contributors” that would link to a page with information about our Artists, Teachers, Writers, Developers etc.
vi. “Jobs” would link to a jobs page
vii. “Blog” would lead to our blog page
viii. “User stories” link to pages with feedback that we obtain from the users about how the content has helped them,
ix. Web 2.0 placeholders for social media (to be added later)

d. The footer of the website should include text “2013 TAVO Sphere, All rights reserved.”

4. The middle block of the front page is the largest in screen real estate and perhaps the most challenging part that requires much creativity and thought on the UI/UX design aspect – the content pages pointed to by the section links on the middle portion of the front page are also being designed.

5. Color preference is towards soft, elegant (think grays, whites, light blues, other light colors) web safe colors. No harsh (too bright, garish) colors.

6. Fonts preference Nice, clean looking fonts (Arial alright) compatible across browsers.

7. Portability and robustness of the front page layout for different platforms should be carefully considered. Although our first launch target platform is PC (where cross browser compatibility is important), this would very soon be followed by mobile devices such as tablets and smartphones given their prevalence across the globe. This mobile friendly design or easy portability to mobile platforms with little work requirement should be considered as a design requirement.

8. Front page as a framework for the complete website: Note that the top and the bottom portions of the front page are envisioned be used as a common template / frame across all the pages of our website – the middle portion would be used to show our content on the other pages of our website.

9. UX: For the UI/UX design, it is critical to keep in mind key qualities such as ease of use, simplicity, elegance and artistic appeal. Some specific points to keep in mind: (1) the major portion of the target audience would be new to English and (2) young children are expected to be the primary audience but we want the website to appeal to adults interested in learning as well, and (3) we need the website to work even with relatively slow Internet speeds (for underdeveloped / developing regions especially), should always be kept in mind. HTML5 compliance ideas are encouraged.

10. Strictly not desired: Typical corporate feel seen in many webpages, blocky graphics, dull and uninviting overall look with no personality, Flash type effects, harsh colors.

11. Creativity and imagination necessary: We would like to reiterate that the designer/developer has complete freedom to re-imagine the front page considering the above requirements and get back with ideas for an inspiring layout that presents the content outlined above in an intuitive format, carefully considering our target audience.

A note: As a rule, we will always make sure that our developers and artists get proper credit for their work and are recognized and acknowledged by everyone visiting our website.

Expected deliverables:
Website design psd files AND coded webpage / Drupal template: the corresponding source code and all the required libraries, images etc would be required with minimal documentation / pointers on how to make changes and customizations.

Interested developers are encouraged to first send us preliminary prototype Design for the front page to get feedback on whether their approach and style is in line with our needs and preferences. We will suggest the developers to proceed further if the team thinks there is some potential for a match (of course, the final determination would be from the pool of shortlisted submissions) – otherwise, in case the team does not see potential for a match with our needs or if we have already received multiple submissions that are comparatively more closely aligned with our vision for the website, we'd prefer to be respectful of the developers’ time and effort by requesting them not to proceed further.

Please consider this effort as your contribution to an important social cause of global and accessible online education and not a commercial enterprise (our passion for making a positive impact is what is driving the TAVO Sphere nonprofit team to undertake this initiative!). We would like to invite you to join us in this effort!

Project Deadline Extended
Reason: Due to requests from interested designers, we are extending the deadline. Looking forward to receiving many other creative designs!

Please see the project brief.

Real Estate

• Please see the project brief.

```html
<!DOCTYPE html>
<html lang="en">
<head>
<meta charset="utf-8">
<title>TAVO Sphere – Basic English Learning</title>
<link href="https://fonts.googleapis.com/css2?family=Arimo:wght@400;700&family=Oswald:wght@500;600&family=Patrick+Hand&display=swap" rel="stylesheet">
<style>
:root{
  --sky:#7fd1f5;
  --sky-deep:#5fc3ef;
  --ink:#444;
  --muted:#777;
  --rule:#d6d6d6;
  --orange:#f7941d;
  --board:#3f5b4c;
  --white:#fff;
  --dark:#333;
}
*{box-sizing:border-box;margin:0;padding:0}
html,body{width:800px;height:1200px;overflow:hidden;background:var(--white)}
body{position:relative;font-family:"Arimo",Arial,sans-serif;color:var(--ink)}
.abs{position:absolute}

.brand{left:88px;top:26px;display:flex;align-items:center;gap:8px}
.brand-dot{width:28px;height:28px;border-radius:50%;background:var(--sky-deep)}
.brand-name{font-weight:700;font-size:21px;color:#5a5a5a;letter-spacing:.5px}

.topbar{left:84px;top:74px;width:634px;height:43px;background:var(--sky)}
.main-nav{left:36px;top:13px;display:flex;gap:14px;font-weight:700;font-size:13px;color:var(--white)}
.main-nav .active{color:#3c3c3c}
.main-nav .active::after{content:"";position:absolute;left:28px;top:30px;border:5px solid transparent;border-top-color:#4a4a4a;border-bottom:0}
.search{left:234px;top:11px;width:230px;height:22px;background:var(--white);display:flex;align-items:center;padding:2px}
.search span{flex:1;font-size:8px;color:#999;padding-left:6px}
.search b{background:var(--orange);color:var(--white);font-size:8px;height:18px;width:52px;display:flex;align-items:center;justify-content:center}
.account{right:20px;top:15px;font-size:9.5px;font-weight:700;color:var(--white)}

.hero{left:84px;top:117px;width:634px;height:260px;background:linear-gradient(135deg,#45624f,#344c40)}
.hero-title{left:60px;top:26px;font-family:"Oswald",sans-serif;color:var(--white);line-height:1}
.hero-title .l1{font-size:40px}
.hero-title .l2{font-size:20px;color:var(--orange);margin-top:4px}
.hero-title .l3{font-size:54px;margin-top:2px}
.learn-btn{left:63px;top:198px;width:134px;height:34px;background:var(--orange);color:var(--white);font-family:"Oswald",sans-serif;font-size:18px;display:flex;align-items:center;justify-content:center;border-radius:2px;box-shadow:0 2px 2px rgba(0,0,0,.3)}
.chalk{left:284px;top:50px;font-family:"Patrick Hand",cursive;font-size:29px;color:var(--white)}
.teacher{left:420px;top:10px;width:214px;height:250px;background:linear-gradient(180deg,#8b7d72,#9cb7d8 55%,#b9d0ec)}
.hero-notch{left:142px;top:250px;border:6px solid transparent;border-bottom:10px solid #d6d6d6;border-top:0}

.dropdown{left:90px;top:117px;width:127px;height:105px;background:rgba(60,60,60,.92);padding:12px 0 0 8px}
.dropdown li{list-style:none;font-size:9px;color:var(--white);height:19.5px;display:flex;align-items:center}
.dropdown li::before{content:"";width:4px;height:4px;border-radius:50%;background:var(--white);margin-right:8px}

.categories{left:84px;top:377px;width:634px;height:48px;display:flex;background:linear-gradient(180deg,#e2e2e2,#9d9d9d)}
.cat{flex:1;display:flex;align-items:center;gap:22px;padding-left:40px;color:var(--white);font-size:12.5px;border-right:1px solid #c9c9c9}
.cat:first-child{flex:0 0 212px}
.cat:last-child{border-right:0;flex:0 0 220px;padding-left:54px}
.cat-a{font-family:Georgia,serif;font-size:22px;color:#666}

.section-title{font-size:13px;color:#555;padding-bottom:6px;border-bottom:1px solid var(--rule)}
.copy{font-size:8.8px;line-height:16px;color:#666;text-align:justify}
.photo{border-radius:1px}

.play{left:153px;top:68px;width:60px;height:34px;background:rgba(40,40,40,.85);border-radius:3px;display:flex;align-items:center;justify-content:center}
.controls{left:16px;top:157px;width:350px;height:18px;background:rgba(40,40,40,.85);border-radius:2px}

.tcol{width:178px}
.quote-open{font-size:16px;font-weight:700;color:#555;line-height:1}
.tcol .copy{padding-left:6px;text-align:justify}
.quote-close{font-weight:700;font-size:13px;color:#444}
.author{font-size:11px;color:#333}
.role{font-size:8.8px;color:#666;margin-top:4px}

.news-title{font-size:9px;font-weight:700;color:#444;line-height:14px}
.news-text{font-size:7.5px;color:#888;line-height:14px}

.footer{left:0;top:957px;width:800px;height:243px;background:var(--sky)}
.fhead{font-size:12.5px;color:#444}
.flinks{list-style:none;font-size:8.5px;color:var(--white)}
.flinks li{height:20px}
.field{width:206px;height:18px;background:var(--white);border:1px solid #ddd;font-size:8.5px;color:#aaa;padding:3px 8px}
.subscribe{left:490px;top:134px;width:66px;height:16px;background:#3a3a3a;color:var(--white);font-size:8.5px;font-weight:700;border-radius:8px;display:flex;align-items:center;justify-content:center}
.social{list-style:none;font-size:9px;color:var(--white)}
.social li{display:flex;align-items:center;justify-content:space-between;width:96px;height:25px}
.social i{width:17px;height:17px;border-radius:50%;background:var(--white)}
.frule{left:0;top:213px;width:800px;height:1px;background:rgba(255,255,255,.45)}
.legal{left:0;top:222px;width:800px;text-align:center;font-size:8.8px;color:var(--white)}
</style>
</head>
<body>

<header>
  <div class="abs brand"><span class="brand-dot"></span><span class="brand-name">TAVO SPHERE</span></div>

  <nav class="abs topbar">
    <div class="abs main-nav"><span class="active">Learn</span><span>About</span><span>Contribute</span></div>
    <div class="abs search"><span>Search here</span><b>SEARCH</b></div>
    <div class="abs account">Login &nbsp;|&nbsp; Sign Up</div>
  </nav>
</header>

<section class="abs hero">
  <div class="abs hero-title">
    <div class="l1">A NON PROFIT</div>
    <div class="l2">ENGLISH LEARNING</div>
    <div class="l3">ONLINE</div>
  </div>
  <div class="abs learn-btn">LEARN NOW</div>
  <div class="abs chalk">Word Learing</div>
  <div class="abs teacher" role="img" aria-label="Smiling teacher in a blue shirt pointing at the chalkboard"></div>
  <div class="abs hero-notch"></div>
</section>

<ul class="abs dropdown">
  <li>Word learning</li>
  <li>Basic sentence learning</li>
  <li>Classic short stories</li>
  <li>Picture Dictionary</li>
</ul>

<nav class="abs categories">
  <div class="cat"><span class="cat-a">a</span>Word learning</div>
  <div class="cat">
    <svg width="12" height="16" viewBox="0 0 12 16"><rect x="1" y="1" width="10" height="14" fill="none" stroke="#666" stroke-width="1.4"/><path d="M3 5h6M3 8h6M3 11h6" stroke="#666" stroke-width="1"/></svg>
    Basic sentence learning</div>
  <div class="cat">
    <svg width="16" height="18" viewBox="0 0 16 18"><rect x="1" y="2" width="14" height="9" fill="none" stroke="#666" stroke-width="1.4"/><path d="M8 11v6M4 17l4-6 4 6M1 1h14" stroke="#666" stroke-width="1.4" fill="none"/></svg>
    Classic stories</div>
</nav>

<main>
  <section class="abs" style="left:83px;top:444px;width:234px">
    <h2 class="section-title" style="font-weight:400">Welcome to TAVO Sphere</h2>
    <div class="photo" role="img" aria-label="Student holding a folder in a library" style="margin-top:10px;height:141px;background:linear-gradient(90deg,#8a5a3a,#d9c0a0 45%,#f2ece4 60%,#9b6a45)"></div>
    <p class="copy" style="margin-top:12px">Lorem Ipsum is simply dummy text of the printing and typesetting industry. Lorem Ipsum has been the industry's standard dummy text ever since the 1500s, when an unknown printer took a galley of type and scrambled it to make a type specimen book. It has survived not only five centuries, but also the leap into electronic typesetting, remaining essentially unchanged.</p>
  </section>

  <section class="abs" style="left:350px;top:444px;width:367px">
    <h2 class="section-title" style="font-weight:400">How it works</h2>
    <div class="abs photo" role="img" aria-label="Students writing at desks in a classroom, video" style="left:0;top:26px;width:367px;height:188px;background:linear-gradient(90deg,#6b7c8a,#c7b8a8 30%,#e8e4df 60%,#d5dde3)">
      <div class="abs play"><svg width="14" height="16" viewBox="0 0 14 16"><path d="M1 1l12 7-12 7z" fill="#fff"/></svg></div>
      <div class="abs controls">
        <div class="abs" style="left:10px;top:6px;width:256px;height:6px;border:1px solid #888"></div>
        <div class="abs" style="left:11px;top:7px;width:112px;height:4px;background:#29a9e0"></div>
        <div class="abs" style="left:275px;top:4px;font-size:8px;font-weight:700;font-style:italic;color:#29a9e0">IIIIII HD</div>
        <div class="abs" style="left:320px;top:4px;width:8px;height:8px;border:1.5px solid #fff"></div>
      </div>
    </div>
    <p class="abs copy" style="left:-2px;top:226px;width:369px">Lorem Ipsum is simply dummy text of the printing and typesetting industry. Lorem Ipsum has been the industry's standard dummy text ever since the 1500s, when an unknown printer took a galley of type and scrambled it to make a type specimen book. It has survived not only five centuries,</p>
  </section>

  <section class="abs" style="left:83px;top:751px;width:394px">
    <h2 class="section-title" style="font-weight:400;padding-bottom:12px">Testimonials</h2>
    <svg class="abs" style="left:359px;top:4px" width="35" height="15" viewBox="0 0 35 15">
      <rect width="14" height="15" fill="#7fd1f5"/><path d="M9 4l-4 3.5 4 3.5z" fill="#fff"/>
      <rect x="21" width="14" height="15" fill="#555"/><path d="M26 4l4 3.5-4 3.5z" fill="#fff"/>
    </svg>
    <article class="abs tcol" style="left:3px;top:36px">
      <div class="quote-open">&#8220;</div>
      <p class="copy">Lorem Ipsum is simply dummy text of the printing and typesetting industry. Lorem Ipsum has been the industry's standard dummy text ever since the 1500s, when an unknown printer took a galley <span class="quote-close">&#8221;</span></p>
      <div class="author" style="margin-top:28px;padding-left:6px">By,Daniel Marsh</div>
      <div class="role" style="padding-left:6px">CEO ,Harbor Consultancy</div>
    </article>
    <article class="abs tcol" style="left:210px;top:36px">
      <div class="quote-open">&#8220;</div>
      <p class="copy">Lorem Ipsum is simply dummy text of the printing and typesetting industry. Lorem Ipsum has been the industry's standard dummy text ever since the 1500s, when an unknown printer took a galley <span class="quote-close">&#8221;</span></p>
      <div class="author" style="margin-top:28px;padding-left:6px">By,Daniel Marsh</div>
      <div class="role" style="padding-left:6px">CEO ,Harbor Consultancy</div>
    </article>
  </section>

  <section class="abs" style="left:510px;top:751px;width:207px">
    <h2 class="section-title" style="font-weight:400;padding:0 0 12px 14px">Latest News</h2>
    <div class="abs" role="img" aria-label="Chalkboard asking do you speak English" style="left:9px;top:33px;width:91px;height:60px;background:linear-gradient(135deg,#3a3a3a,#222)"></div>
    <div class="abs" style="left:100px;top:31px;width:107px">
      <div class="news-title">Lorem ipsum dolor sit amet</div>
      <div class="news-text">Ut labore et dolore magna aliqua. Ut enim ad minim veniam, quis nostrud labo-ris nisi ut aliquip.</div>
    </div>
    <div class="abs" role="img" aria-label="Smiling student holding books" style="left:13px;top:127px;width:80px;height:58px;background:linear-gradient(90deg,#b98a5a,#3e8c95 50%,#c8a27a)"></div>
    <div class="abs" style="left:100px;top:124px;width:107px">
      <div class="news-title">Iste natus error sit voluptatem</div>
      <div class="news-text">Ut labore et dolore magna aliqua. Ut enim ad minim</div>
    </div>
  </section>
</main>

<footer class="abs footer">
  <div class="abs" style="left:84px;top:22px">
    <h3 class="fhead" style="font-weight:400">Menu Links</h3>
    <ul class="flinks" style="margin-top:20px">
      <li>Help</li><li>Contact us</li><li>For teachers</li><li>Volunteer</li>
      <li>Contributors</li><li>Jobs</li><li>Blog</li><li>User stories</li>
    </ul>
  </div>
  <div class="abs" style="left:216px;top:22px">
    <h3 class="fhead" style="font-weight:400">Support Links</h3>
    <ul class="flinks" style="margin-top:18px">
      <li>Legal Notice</li><li>Privacy Policy</li><li>Terms &amp; Conditions</li><li>Help</li>
    </ul>
  </div>
  <div class="abs" style="left:350px;top:22px;width:210px">
    <h3 class="fhead" style="font-weight:400">Newsletter SignUp</h3>
    <p style="font-size:8.5px;line-height:16px;color:var(--white);margin-top:10px">Sign-up for our daily emails by entering your information below:</p>
  </div>
  <div class="abs field" style="left:350px;top:81px">Name</div>
  <div class="abs field" style="left:350px;top:109px">Enter Your E-Mail ID</div>
  <div class="abs subscribe">Subscribe</div>
  <div class="abs" style="left:618px;top:22px">
    <h3 class="fhead" style="font-weight:400">Connect With Us</h3>
    <ul class="social" style="margin-top:10px">
      <li>Chirpline<i></i></li><li>Circlebook<i></i></li><li>Worknet<i></i></li>
    </ul>
  </div>
  <div class="abs frule"></div>
  <div class="abs legal">2013 TAVO Sphere, All rights reserved</div>
</footer>

</body>
</html>
```